Create modern and sleek business card for luxury real estate company

We're a "boutique" real estate office looking for a design that gets across a highly modern luxury brand. Blacks and whites are probably the best colors unless we try a silver foil for the logo. I've attached a version of our current logo here. I'd like to swap out the current font on there with Gotham Light Regular.

I'm looking to have one side of the card have the logo with the space for our agents info on the other side.

Target Market(s)

Young professionals in a "luxury" headspace

Industry/Entity Type

Real estate

Contact Information for Business Card

A place for agent name, cell number, website. The slogan "Simply Rethinking Real Estate".

Font styles to use
Other font styles liked:
• Gotham Regular

Colors

Designer to choose only greyscale colors for use in the design.

Requirements
Must have
• Matte black as the background color. Clean lines and use of contrast. A specific design aspect that will use silver foil.
Nice to have
• Up in the air on integrating a QR code
Should not have
• Any houses or other real estate related design (ex: a clip art house)

```html
<!DOCTYPE html>
<html lang="en">
<head>
<meta charset="utf-8">
<title>Halden Estates – Business Card</title>
<link href="https://fonts.googleapis.com/css2?family=Cinzel:wght@400;600&family=Lato:wght@400&display=swap" rel="stylesheet">
<style>
  :root{
    --stage:#1c1c1c;
    --card-black:#2e2e2e;
    --card-white:#ffffff;
    --ink-light:#f2f2f2;
    --ink-dark:#1a1a1a;
    --ring-grey:#3a3a3a;
  }
  html,body{margin:0;padding:0;overflow:hidden;}
  body{width:1200px;height:1015px;background:var(--stage);position:relative;
       font-family:"Lato",sans-serif;}
  .card{position:absolute;left:250px;width:700px;height:400px;overflow:hidden;
        box-shadow:0 14px 30px rgba(0,0,0,.55);}
  .card--front{top:60px;background:var(--card-black);}
  .card--back{top:555px;background:var(--card-black);}

  .brand{position:absolute;display:flex;align-items:center;gap:18px;}
  .brand__circle{width:96px;height:96px;border-radius:50%;border:2px solid currentColor;box-sizing:border-box;}
  .brand__name{font-family:"Cinzel",serif;font-weight:400;font-size:44px;line-height:1.05;letter-spacing:1px;}
  .card--front .brand{left:150px;top:140px;color:var(--ink-light);}

  .back-art{position:absolute;inset:0;}
  .card--back .brand{right:50px;top:70px;flex-direction:column;gap:14px;color:var(--ink-dark);}
  .card--back .brand__circle{width:84px;height:84px;}
  .card--back .brand__name{font-size:38px;text-align:center;}

  .agent{position:absolute;left:50px;top:80px;color:var(--ink-light);}
  .agent__name{font-family:"Cinzel",serif;font-size:24px;letter-spacing:1px;margin:0;}
  .agent__title{font-size:15px;margin:2px 0 0;}
  .contact{position:absolute;left:50px;top:215px;color:var(--ink-light);font-size:15px;line-height:1.45;}
  .contact p{margin:0;}
  .contact ul{list-style:none;margin:16px 0 0;padding:0;}
  .contact li{display:flex;align-items:center;gap:8px;}
  .contact svg{width:14px;height:14px;fill:none;stroke:var(--ink-light);stroke-width:1.6;}
</style>
</head>
<body>
  <section class="card card--front">
    <div class="brand">
      <div class="brand__circle"></div>
      <div class="brand__name">HALDEN<br>ESTATES</div>
    </div>
  </section>

  <section class="card card--back">
    <svg class="back-art" viewBox="0 0 700 400" aria-hidden="true">
      <circle cx="545" cy="150" r="262" fill="var(--ring-grey)"/>
      <circle cx="560" cy="140" r="255" fill="var(--card-white)"/>
    </svg>
    <div class="agent">
      <h1 class="agent__name">MARCUS HALE</h1>
      <p class="agent__title">Managing Director</p>
    </div>
    <div class="contact">
      <p>88 Larch Avenue</p>
      <p>Northfield, 45100</p>
      <ul>
        <li><svg viewBox="0 0 16 16"><path d="M4 2l2 3-1.5 1.5a8 8 0 0 0 5 5L11 10l3 2-1 2.5C7 14 2 9 1.5 3z"/></svg>044-555 010 202</li>
        <li><svg viewBox="0 0 16 16"><rect x="1.5" y="3.5" width="13" height="9"/><path d="M1.5 3.5l6.5 5 6.5-5"/></svg>info@haldenestates.com</li>
        <li><svg viewBox="0 0 16 16"><circle cx="8" cy="8" r="6.5"/><path d="M1.5 8h13M8 1.5c-3 3.5-3 9.5 0 13M8 1.5c3 3.5 3 9.5 0 13"/></svg>www.haldenestates.com</li>
      </ul>
    </div>
    <div class="brand">
      <div class="brand__circle"></div>
      <div class="brand__name">HALDEN<br>ESTATES</div>
    </div>
  </section>
</body>
</html>
```